Harborline Auto LLC

Car Dealer Customer Service
Address: 2874 Cresthaven Road, Shelbyville, TN 37162
web: www.harborlineautoxq.net
email: harborlineautoxq@mailnest.example
Phone: (931) 555-0148
Phone: (629) 555-0173

```html
<!DOCTYPE html>
<html lang="en">
<head>
<meta charset="utf-8">
<title>Harborline Auto – Business Card</title>
<link rel="stylesheet" href="https://fonts.googleapis.com/css2?family=Poppins:wght@400;500;600;700&display=swap">
<style>
  :root {
    --page-bg: #e6e2dd;
    --card-bg: #f1f2f2;
    --brand-blue: #1f6e93;
    --brand-teal: #23799f;
    --accent-gold: #d99d22;
    --ink: #2a2a2a;
  }
  html, body {
    margin: 0;
    padding: 0;
    width: 1200px;
    height: 1054px;
    overflow: hidden;
    background: var(--page-bg);
    font-family: "Poppins", sans-serif;
  }
  .business-card {
    position: absolute;
    left: 100px;
    top: 227px;
    width: 1000px;
    height: 600px;
    background: var(--card-bg);
    border-radius: 26px;
    overflow: hidden;
    box-shadow: 0 12px 36px rgba(0,0,0,0.12);
  }
  .company-name {
    position: absolute;
    left: 44px;
    top: 62px;
    margin: 0;
    font-size: 50px;
    font-weight: 700;
    letter-spacing: 1px;
    color: var(--brand-blue);
    text-transform: uppercase;
  }
  .person-name {
    position: absolute;
    left: 44px;
    top: 240px;
    margin: 0;
    font-size: 37px;
    font-weight: 600;
    color: var(--brand-blue);
  }
  .person-role {
    position: absolute;
    left: 44px;
    top: 290px;
    margin: 0;
    font-size: 27px;
    font-weight: 400;
    color: var(--ink);
  }
  .contact-list {
    position: absolute;
    left: 44px;
    top: 367px;
    margin: 0;
    padding: 0;
    list-style: none;
  }
  .contact-item {
    display: flex;
    align-items: center;
    height: 36px;
    font-size: 26px;
    color: var(--ink);
  }
  .contact-item.phone {
    font-weight: 700;
    color: var(--brand-blue);
    letter-spacing: 0.5px;
  }
  .contact-item.phone + .contact-item.web { margin-top: 8px; }
  .contact-icon {
    width: 24px;
    height: 24px;
    margin-right: 18px;
    flex: none;
  }
  .contact-address {
    position: absolute;
    left: 44px;
    top: 522px;
    margin: 0;
    font-size: 26px;
    color: var(--ink);
  }
  .brand-mark {
    position: absolute;
    left: 534px;
    top: 45px;
    width: 520px;
    height: 520px;
  }
</style>
</head>
<body>
  <div class="business-card">
    <h1 class="company-name">Harborline Auto</h1>

    <h2 class="person-name">Daniel Averin</h2>
    <p class="person-role">Managing Director</p>

    <ul class="contact-list">
      <li class="contact-item phone">
        <svg class="contact-icon" viewBox="0 0 24 24" aria-hidden="true">
          <path fill="var(--accent-gold)" d="M6.6 10.8a15.5 15.5 0 0 0 6.6 6.6l2.2-2.2c.3-.3.7-.4 1-.2 1.1.4 2.3.6 3.6.6.6 0 1 .4 1 1V20c0 .6-.4 1-1 1A17 17 0 0 1 3 4c0-.6.4-1 1-1h3.5c.6 0 1 .4 1 1 0 1.3.2 2.5.6 3.6.1.3 0 .7-.2 1z"/>
        </svg>
        931-555-0148
      </li>
      <li class="contact-item phone">
        <svg class="contact-icon" viewBox="0 0 24 24" aria-hidden="true">
          <path fill="var(--accent-gold)" d="M6.6 10.8a15.5 15.5 0 0 0 6.6 6.6l2.2-2.2c.3-.3.7-.4 1-.2 1.1.4 2.3.6 3.6.6.6 0 1 .4 1 1V20c0 .6-.4 1-1 1A17 17 0 0 1 3 4c0-.6.4-1 1-1h3.5c.6 0 1 .4 1 1 0 1.3.2 2.5.6 3.6.1.3 0 .7-.2 1z"/>
        </svg>
        629-555-0173
      </li>
      <li class="contact-item web">
        <svg class="contact-icon" viewBox="0 0 24 24" aria-hidden="true">
          <rect x="2" y="5" width="20" height="14" rx="1.5" fill="var(--accent-gold)"/>
          <path d="M3 6.5l9 6.5 9-6.5" fill="none" stroke="var(--card-bg)" stroke-width="1.6"/>
        </svg>
        www.harborlineautoxq.net
      </li>
      <li class="contact-item email">
        <svg class="contact-icon" viewBox="0 0 24 24" aria-hidden="true">
          <circle cx="12" cy="12" r="10" fill="var(--accent-gold)"/>
          <path d="M2 12h20M12 2c3 3 3 17 0 20M12 2c-3 3-3 17 0 20" fill="none" stroke="var(--card-bg)" stroke-width="1.4"/>
        </svg>
        harborlineautoxq@mailnest.example
      </li>
    </ul>

    <p class="contact-address">2874 Cresthaven Road, Shelbyville, TN 37162</p>

    <svg class="brand-mark" viewBox="0 0 520 520" role="img" aria-label="Brand emblem area">
      <circle cx="260" cy="260" r="205" fill="none" stroke="var(--brand-teal)" stroke-width="70"/>
    </svg>
  </div>
</body>
</html>
```